Business Card for premium dental clinic

We are a premium dental clinic based in Brasov, Romania with more than 15 year on the market, providing quality dental treatment made by a team of more specialized dentists, working with modern equipment as a solution to beautiful and healthy teeth.

Our current logo for the clinic use 2 square with colors black and gold - dr Ternisu - studio, using family fonts Bodoni, Myriad Pro and Segoe Print.
Depending on the printing we used some gold CMYK background or gold foil picture background or a gold gradient.
We want a business card:
- eye catching business card
- distinguished business card
- premium design
- to keep the color scheme of black and gold
- to attract the customers to spent time reading the information
- modern concept

```html
<!DOCTYPE html>
<html lang="en">
<head>
<meta charset="utf-8">
<title>dr Ternisu Dental Studio – Business Card</title>
<link href="https://fonts.googleapis.com/css2?family=Lato:wght@400;700&display=swap" rel="stylesheet">
<style>
  :root {
    --gold: #bb8b2e;
    --black: #060606;
    --paper: #f3f3f3;
    --white: #ffffff;
    --ink: #1e1e1e;
    --rule: #c9c9c9;
    --stage: #dcdcdc;
  }
  * { margin: 0; padding: 0; box-sizing: border-box; }
  html, body {
    width: 1200px; height: 1015px; overflow: hidden;
    background: var(--stage);
    font-family: "Lato", Arial, sans-serif;
  }
  .card {
    position: absolute;
    width: 620px; height: 350px;
    overflow: hidden;
    box-shadow: 0 10px 30px rgba(0,0,0,.25);
  }

  /* Front face */
  .card--front { left: 110px; top: 90px; display: flex; }
  .front__gold { width: 45%; background: var(--gold); }
  .front__black {
    width: 55%; background: var(--black);
    display: flex; align-items: center; justify-content: center;
  }
  .brand-name {
    font-family: "Lato", Arial, sans-serif;
    font-weight: 400;
    color: var(--white);
    font-size: 40px;
    line-height: 1.15;
    text-align: center;
  }

  /* Back face */
  .card--back { left: 470px; top: 560px; background: var(--paper); }
  .back__logo {
    position: absolute; left: 50px; top: 120px;
    display: flex; align-items: center; gap: 14px;
  }
  .back__logo-mark { width: 34px; height: 34px; background: var(--gold); }
  .back__logo .brand-name { color: var(--black); font-size: 24px; text-align: left; }
  .back__divider {
    position: absolute; left: 345px; top: 40px; width: 1px; height: 190px;
    background: var(--rule);
  }
  .contact { position: absolute; left: 370px; top: 48px; color: var(--ink); }
  .contact__name {
    color: var(--gold); font-weight: 700; font-size: 19px;
    text-transform: uppercase; letter-spacing: .3px;
  }
  .contact__role { font-size: 15px; margin-bottom: 8px; }
  .contact__line {
    display: flex; align-items: center; gap: 8px;
    font-size: 15px; line-height: 22px;
  }
  .contact__line svg { width: 13px; height: 13px; fill: var(--gold); flex: none; }
  .contact__address { font-size: 15px; line-height: 21px; margin-top: 6px; }
  .back__band {
    position: absolute; left: 0; bottom: 0; width: 58%; height: 14px;
    background: var(--gold);
  }
</style>
</head>
<body>

<section class="card card--front" aria-label="Card front">
  <div class="front__gold"></div>
  <div class="front__black">
    <p class="brand-name">dr Ternisu<br>Dental Studio</p>
  </div>
</section>

<section class="card card--back" aria-label="Card back">
  <div class="back__logo">
    <span class="back__logo-mark"></span>
    <p class="brand-name">dr Ternisu<br>Dental Studio</p>
  </div>

  <div class="back__divider"></div>

  <div class="contact">
    <p class="contact__name">Andrei Moldovan</p>
    <p class="contact__role">Managing Director</p>
    <p class="contact__line">
      <svg viewBox="0 0 16 16" aria-hidden="true"><path d="M3.6 1.2l2.6 2.6-1.5 2a9 9 0 0 0 5.5 5.5l2-1.5 2.6 2.6-1.6 2.4C7.4 15.6.4 8.6 1.2 2.8z"/></svg>
      0268 410 275
    </p>
    <p class="contact__line">
      <svg viewBox="0 0 16 16" aria-hidden="true"><path d="M1 3h14v10H1zM2.5 4.5v.6L8 9l5.5-3.9v-.6z"/></svg>
      hello@ternisu.ro
    </p>
    <p class="contact__line">
      <svg viewBox="0 0 16 16" aria-hidden="true"><path d="M8 .5a5.5 5.5 0 0 0-5.5 5.5C2.5 10 8 15.5 8 15.5S13.5 10 13.5 6A5.5 5.5 0 0 0 8 .5zm0 7.6A2.1 2.1 0 1 1 8 3.9a2.1 2.1 0 0 1 0 4.2z"/></svg>
      www.ternisu.ro
    </p>
    <p class="contact__address">17 Strada Lunga<br>Brasov, 500035</p>
  </div>

  <div class="back__band"></div>
</section>

</body>
</html>
```